ZEFRA Ice Cream Logo & Packaging Project

We need a logo and ice cream packaging for our new company Zefra.

The company is based in Freetown, Sierra Leone, West Africa. It will be a large scale business, going national. For example the minimum order is 120.000 pieces of the small cup. Zefra will produce and sell affordable frozen dairy products directly to consumers through a unique street vending system.

Your design will have great exposure.

The word ZEFRA refers to anything or something which is WONDERFUL OR EXTRAORDINARY. ZEFRA is something EXPLOSIVE. Also ZEFRA refers to a shape, The ZEFRA shape is round,just like an ICE CREAM BALL.

We thought the design could incorporate and exploding rays around an ice cream ball or cone. The market responds well to colours and visuals.

People may use the word ZEFRA in this context :

1-A man who has a very nice STRONG and TONED,and full of MUSCLES body is a ZEFRA
2 -A great EVENT,big HUGE CONCERT is a ZEFRA
3 -A powerful and tasty ICE CREAM is a ZEFRA.

There are several packagings to design. See attached documents for sizes, but the first task is the logo and the small cup.

The lid will be transparent plastic so you can see the ice cream, so we don't need the flavours on the label.

100-120ml tub Small cup sleeve and full lid

Required info includes :

Talvo Ice Cream Co, Wellington, Freetown, Sierra Leone.

Ingredients : sugar, glucose solids, milk, bean gum, natural flavour, colour, milk chocolate

Afterwards we will need packaging for :

1050ml oval tub sleeve and full lid

2120ml oval tub sleeve and lid full

standard ice cream cone sleeve.

standard ice lolly sleeve (note sleeve will be transparent)

trolley cart image 60cm wide x 60cm heigh approx

Target Market(s)

All ages and nationalities. The company is based in Freetown, Sierra Leone, West Africa which is a 3rd world country. The market respond well to colours and visuals.

Industry/Entity Type

It Company

Font styles to use
Serif
Sans Serif

Requirements
Must have
• Talvo Ice Cream Co, Wellington, Freetown, Sierra Leone.
• Ingredients : sugar, glucose solids, milk, bean gum, natural flavour, colour, milk chocolate.
Nice to have
• The word ZEFRA refers to anything or something which is WONDERFUL OR EXTRAORDINARY. ZEFRA is something EXPLOSIVE. Also ZEFRA refers to a shape, The ZEFRA shape is round,just like an ICE CREAM BALL.
• We thought the design could incorporate and exploding rays around an ice cream ball or cone.

```html
<!DOCTYPE html>
<html lang="en">
<head>
<meta charset="utf-8">
<title>Zefra Ice Cream – Small Cup Sleeve</title>
<link href="https://fonts.googleapis.com/css2?family=Fredoka:wght@500;600;700&family=Montserrat:wght@600;700&family=Questrial&display=swap" rel="stylesheet">
<style>
  :root{
    --cocoa-dark:#3b2213;
    --cocoa:#5a3a24;
    --ray-light:#e6d6c4;
    --ray-mid:#b08b6c;
    --ray-edge:#6e4c34;
    --panel:#9a7758;
    --panel-light:#a98566;
    --cream:#fff8ee;
    --scoop-light:#e8cfa4;
    --scoop-mid:#b98d5e;
    --scoop-dark:#6b4228;
  }
  *{box-sizing:border-box;margin:0;padding:0}
  html,body{width:1200px;height:527px;overflow:hidden;background:#ffffff}
  .sleeve{position:relative;width:1200px;height:527px;overflow:hidden;font-family:"Questrial",sans-serif;color:var(--cocoa-dark)}

  /* front panel */
  .front{position:absolute;left:0;top:0;width:712px;height:527px;
    background:radial-gradient(circle at 350px 190px,var(--ray-light) 0,var(--ray-mid) 240px,var(--ray-edge) 520px)}
  .front-band{position:absolute;left:0;top:0;width:712px;height:527px}
  .front-tagline{position:absolute;left:27px;top:16px;font-family:"Montserrat",sans-serif;font-weight:700;font-size:22px;color:var(--cocoa-dark)}
  .brand-name{position:absolute;left:0;width:712px;top:196px;text-align:center;font-family:"Fredoka",sans-serif;font-weight:700;font-size:68px;letter-spacing:2px;color:var(--cocoa-dark)}
  .scoop-photo{position:absolute;left:220px;top:258px;width:454px;height:300px;border-radius:50% 50% 10% 10% / 62% 62% 10% 10%;
    background:radial-gradient(ellipse at 45% 35%,var(--scoop-light) 0,var(--scoop-mid) 55%,var(--scoop-dark) 100%)}
  .flavour-badge{position:absolute;left:104px;top:292px;width:120px;height:120px;border-radius:50%;background:var(--cream);border:12px solid var(--cocoa-dark);
    display:flex;align-items:center;justify-content:center;text-align:center;font-family:"Montserrat",sans-serif;font-weight:700;font-size:21px;line-height:1.15;color:var(--cocoa-dark)}
  .net-volume{position:absolute;left:12px;top:468px;font-family:"Fredoka",sans-serif;font-weight:600;font-size:24px;color:var(--cream)}

  /* back panel */
  .back{position:absolute;left:712px;top:0;width:488px;height:527px;background:linear-gradient(90deg,var(--panel) 0,var(--panel-light) 100%)}
  .side-copy{position:absolute;left:-148px;top:218px;width:340px;transform:rotate(-90deg);font-size:11px;line-height:1.35;color:var(--cocoa-dark)}

  .nutrition{position:absolute;left:41px;top:18px;width:254px;height:482px;border:4px solid var(--cocoa-dark);border-radius:16px;padding:6px 12px 0 14px;font-size:13px}
  .nutrition-title{font-family:"Fredoka",sans-serif;font-weight:600;font-size:23px;line-height:1;margin-bottom:5px;margin-left:6px}
  .nutrition-line{padding-left:6px;line-height:18px}
  .nutrition-row{padding-left:6px;line-height:22px;border-bottom:1.5px solid var(--cocoa-dark);height:25px;padding-top:2px}
  .bar-thick{height:16px;background:var(--cocoa-dark);margin:5px 0 6px}
  .bar-mid{height:5px;background:var(--cocoa-dark);margin:2px 0}
  .nutrition-grid{display:grid;grid-template-columns:1fr 1fr;font-size:12.5px;line-height:17px;margin-top:6px}

  .ingredients{position:absolute;left:309px;top:26px;width:172px}
  .ingredients-title{font-family:"Fredoka",sans-serif;font-weight:500;font-size:21px;line-height:1.1}
  .ingredients-list{font-size:15px;line-height:18px;margin-top:2px}
  .sample-title{position:absolute;left:309px;top:162px;font-size:13px}
  .sample-copy{position:absolute;left:309px;top:180px;width:172px;font-size:7.5px;line-height:9.5px}
  .icon-slots{position:absolute;left:312px;top:292px;display:flex;gap:10px}
  .icon-slot{width:45px;height:44px;background:#ffffff}
  .icon-caption{position:absolute;left:312px;width:155px;top:348px;text-align:center;font-style:italic;font-size:12px;color:var(--cream)}
  .barcode-area{position:absolute;left:306px;top:406px;width:167px;height:82px;background:var(--cocoa-dark);color:var(--cream);
    display:flex;align-items:center;justify-content:center;font-size:19px}
</style>
</head>
<body>
<main class="sleeve">
  <section class="front">
    <svg class="front-band" viewBox="0 0 712 527" aria-hidden="true">
      <path d="M0 420 Q230 340 712 350 L712 527 L0 527 Z" fill="var(--cocoa)"/>
      <path d="M0 404 Q230 326 712 336" fill="none" stroke="var(--cocoa-dark)" stroke-width="10"/>
    </svg>
    <p class="front-tagline">"Place Text Here"</p>
    <h1 class="brand-name">ZEFRA</h1>
    <div class="scoop-photo" role="img" aria-label="Photo of a scoop of chocolate and vanilla swirl ice cream with cookie pieces"></div>
    <div class="flavour-badge">Choco<br>late</div>
    <p class="net-volume">Netto :120 ml</p>
  </section>

  <section class="back">
    <p class="side-copy">Lorem ipsum dolor sit amet, consectetuer adipiscing elit, sed diam nonummy nibh euismod tincid.</p>

    <div class="nutrition">
      <h2 class="nutrition-title">Nutrition Facts</h2>
      <p class="nutrition-line">Place Text Here</p>
      <p class="nutrition-line">Place Text Here</p>
      <div class="bar-thick"></div>
      <p class="nutrition-line">Place Text Here</p>
      <div class="bar-mid"></div>
      <p class="nutrition-line">Place Text Here</p>
      <div class="bar-mid"></div>
      <p class="nutrition-row">Place Text Here</p>
      <p class="nutrition-row">Place Text Here</p>
      <p class="nutrition-row">Place Text Here</p>
      <p class="nutrition-row">Place Text Here</p>
      <p class="nutrition-row">Place Text Here</p>
      <p class="nutrition-row">Place Text Here</p>
      <p class="nutrition-row">Place Text Here</p>
      <p class="nutrition-row">Place Text Here</p>
      <p class="nutrition-line" style="margin-top:3px">Place Text Here</p>
      <div class="bar-mid"></div>
      <div class="nutrition-grid">
        <span>Place Text Here</span><span>Place Text Here</span>
        <span>Place Text Here</span><span>Place Text Here</span>
        <span>Place Text Here</span><span>Place Text Here</span>
        <span>Place Text Here</span><span>Place Text Here</span>
      </div>
    </div>

    <div class="ingredients">
      <h2 class="ingredients-title">Ingredients :</h2>
      <p class="ingredients-list">sugar, glucose solids, milk, bean gum, natural flavour, colour, milk chocolate</p>
    </div>
    <p class="sample-title">SAMPLE TEXT</p>
    <p class="sample-copy">Talvo Ice Cream Co, Wellington, Freetown, Sierra Leone. Keep frozen at minus eighteen degrees. Do not refreeze once thawed. Best before date and batch number are printed on the base of the cup.</p>
    <div class="icon-slots">
      <div class="icon-slot"></div><div class="icon-slot"></div><div class="icon-slot"></div>
    </div>
    <p class="icon-caption">"Picture Icon"</p>
    <div class="barcode-area">Barcode</div>
  </section>
</main>
</body>
</html>
```